real esate business card with company logo and name

we need a business card design for a real esate company

The company name is Walsh & Brand Pty Ltd, and we have our logo designed and will upload. We want classic or moden feel. Black or white background. looks more textured. Should include folowinginformations
Owen Walsh and Lucy Brand
Sales Agents & Onsite Manager
p: 07 5948 2063
F: 07 5948 2174
M:0431 857 219
3/42 Marlow Crescent, FERNLEA QLD 4213

We want this business card looks professonal. Thank you in advance.

Industry/Entity Type

Real Estate Agent

Contact Information for Business Card

Owen Walsh and Lucy Brand
Onsite Manager & Sales Agents
p: 07 5948 2063
M:0431 857 219

Font styles to use
Serif

Colors
000000
fbfbfb
333333
959595

Requirements
Must have
• company logo and name, black or white back ground

```html
<!DOCTYPE html>
<html lang="en">
<head>
<meta charset="utf-8">
<title>Walsh &amp; Brand Pty Ltd – Business Card</title>
<link href="https://fonts.googleapis.com/css2?family=Tinos:wght@400;700&display=swap" rel="stylesheet">
<style>
  :root {
    --black: #000000;
    --paper: #fbfbfb;
    --paper-shade: #d9d9d9;
    --charcoal: #333333;
    --silver: #959595;
    --stage: #e4e4e4;
  }
  html, body {
    margin: 0;
    width: 1189px;
    height: 1200px;
    overflow: hidden;
    background: var(--stage);
    font-family: "Tinos", "Times New Roman", serif;
  }
  .card {
    position: absolute;
    left: 140px;
    width: 918px;
    height: 523px;
    overflow: hidden;
    background: radial-gradient(ellipse at 62% 30%, var(--paper) 0%, #efefef 45%, var(--paper-shade) 100%);
  }
  .card--first { top: 46px; }
  .card--second { top: 623px; }
  .card__wave { position: absolute; inset: 0; }
  .brand {
    position: absolute;
    left: 101px;
    top: 90px;
    width: 260px;
    text-align: center;
  }
  .brand__mark {
    display: block;
    width: 100px;
    height: 100px;
    margin: 0 auto 26px;
    background: var(--silver);
  }
  .brand__name {
    font-size: 24px;
    color: var(--charcoal);
    letter-spacing: 1px;
    text-transform: uppercase;
    white-space: nowrap;
  }
  .people {
    position: absolute;
    right: 61px;
    top: 44px;
    text-align: right;
  }
  .person { margin-bottom: 14px; }
  .person__name {
    font-size: 39px;
    color: var(--black);
    line-height: 1.05;
  }
  .person__role {
    font-size: 26px;
    color: var(--charcoal);
    line-height: 1.05;
  }
  .contacts {
    position: absolute;
    right: 61px;
    top: 357px;
    list-style: none;
    margin: 0;
    padding: 0;
    color: var(--paper);
    font-size: 25px;
  }
  .contact {
    display: flex;
    justify-content: flex-end;
    align-items: flex-start;
    line-height: 32px;
    min-height: 33px;
  }
  .contact__text { text-align: right; }
  .contact__icon {
    flex: none;
    width: 21px;
    height: 21px;
    margin: 5px 0 0 32px;
    background: var(--paper);
  }
</style>
</head>
<body>

<section class="card card--first">
  <svg class="card__wave" width="918" height="523" viewBox="0 0 918 523" aria-hidden="true">
    <path d="M0,297 C180,330 330,335 450,300 C560,268 640,250 700,262 C800,282 870,312 918,336 L918,523 L0,523Z" fill="var(--charcoal)"/>
    <path d="M0,355 C200,382 380,386 520,336 C640,292 760,286 918,340" fill="none" stroke="var(--silver)" stroke-width="4"/>
    <path d="M0,360 C200,388 380,392 520,342 C640,298 760,293 918,346 L918,523 L0,523Z" fill="var(--black)"/>
  </svg>
  <div class="brand"><span class="brand__mark"></span><div class="brand__name">Walsh &amp; Brand Pty Ltd.</div></div>
  <div class="people">
    <div class="person"><div class="person__name">Owen Walsh</div><div class="person__role">Onsite Manager</div></div>
    <div class="person"><div class="person__name">Lucy Brand</div><div class="person__role">Sales Agents</div></div>
  </div>
  <ul class="contacts">
    <li class="contact"><span class="contact__text">07 5948 2063</span>
      <svg class="contact__icon" viewBox="0 0 21 21" aria-label="phone"><path d="M6,4 L9,4 L10,8 L8,9 C9,11 10,12 12,13 L13,11 L17,12 L17,15 C11,16 5,10 6,4Z" fill="var(--black)"/></svg></li>
    <li class="contact"><span class="contact__text">0431 857 219</span>
      <svg class="contact__icon" viewBox="0 0 21 21" aria-label="mobile"><rect x="6" y="3" width="9" height="15" rx="1.5" fill="var(--black)"/><rect x="7.5" y="5" width="6" height="5" fill="var(--paper)"/></svg></li>
    <li class="contact"><span class="contact__text">3/42 Marlow Crescent,<br>FERNLEA QLD 4213</span>
      <svg class="contact__icon" viewBox="0 0 21 21" aria-label="address"><path d="M10.5,3 C7.5,3 6,5.3 6,7.5 C6,10.5 10.5,17 10.5,17 C10.5,17 15,10.5 15,7.5 C15,5.3 13.5,3 10.5,3Z" fill="var(--black)"/><circle cx="10.5" cy="7.5" r="1.8" fill="var(--paper)"/></svg></li>
  </ul>
</section>

<section class="card card--second">
  <svg class="card__wave" width="918" height="523" viewBox="0 0 918 523" aria-hidden="true">
    <path d="M0,297 C180,330 330,335 450,300 C560,268 640,250 700,262 C800,282 870,312 918,336 L918,523 L0,523Z" fill="var(--charcoal)"/>
    <path d="M0,355 C200,382 380,386 520,336 C640,292 760,286 918,340" fill="none" stroke="var(--silver)" stroke-width="4"/>
    <path d="M0,360 C200,388 380,392 520,342 C640,298 760,293 918,346 L918,523 L0,523Z" fill="var(--black)"/>
  </svg>
  <div class="brand"><span class="brand__mark"></span><div class="brand__name">Walsh &amp; Brand Pty Ltd.</div></div>
  <div class="people">
    <div class="person"><div class="person__name">Owen Walsh</div><div class="person__role">Onsite Manager</div></div>
    <div class="person"><div class="person__name">Lucy Brand</div><div class="person__role">Sales Agents</div></div>
  </div>
  <ul class="contacts">
    <li class="contact"><span class="contact__text">07 5948 2063</span>
      <svg class="contact__icon" viewBox="0 0 21 21" aria-label="phone"><path d="M6,4 L9,4 L10,8 L8,9 C9,11 10,12 12,13 L13,11 L17,12 L17,15 C11,16 5,10 6,4Z" fill="var(--black)"/></svg></li>
    <li class="contact"><span class="contact__text">0431 857 219</span>
      <svg class="contact__icon" viewBox="0 0 21 21" aria-label="mobile"><rect x="6" y="3" width="9" height="15" rx="1.5" fill="var(--black)"/><rect x="7.5" y="5" width="6" height="5" fill="var(--paper)"/></svg></li>
    <li class="contact"><span class="contact__text">3/42 Marlow Crescent,<br>FERNLEA QLD 4213</span>
      <svg class="contact__icon" viewBox="0 0 21 21" aria-label="address"><path d="M10.5,3 C7.5,3 6,5.3 6,7.5 C6,10.5 10.5,17 10.5,17 C10.5,17 15,10.5 15,7.5 C15,5.3 13.5,3 10.5,3Z" fill="var(--black)"/><circle cx="10.5" cy="7.5" r="1.8" fill="var(--paper)"/></svg></li>
  </ul>
</section>

</body>
</html>
```